TalkHarbor - Language Coaching Services

Sleek, innovative, trendy design for Language Coaching business.

TalkHarbor is a new UK based company that provides Language Coaching services. We offer highly personalized on-line and face to face language courses. We also impart learning techniques workshops based on the latest neuroscience research for second-language acquisition.

Target Market(s)

See attached info

Industry/Entity Type

Consulting

Contact Information for Business Card

TalkHarbor
DaniaKV@talkharbor.co.uk
TalkHarbor.co.uk
London, UK

Font styles to use
Sans Serif

```html
<!DOCTYPE html>
<html lang="en">
<head>
<meta charset="UTF-8">
<title>TalkHarbor Business Card</title>
<link rel="stylesheet" href="https://fonts.googleapis.com/css2?family=Montserrat:wght@400;500;700&display=swap">
<style>
  :root {
    --page-bg: #e9ebee;
    --card-white: #ffffff;
    --brand-blue: #1a9bd6;
    --deep-blue: #0d6aa0;
    --name-blue: #0f6d9e;
    --title-grey: #8a8a8a;
    --text-grey: #555a5e;
    --back-light: #00b4ee;
    --back-mid: #0a8cc8;
    --back-dark: #07527f;
  }
  * { margin: 0; padding: 0; box-sizing: border-box; }
  html, body { width: 1125px; height: 1200px; overflow: hidden; }
  body {
    background: var(--page-bg);
    font-family: "Montserrat", sans-serif;
    position: relative;
  }
  .card {
    position: absolute;
    left: 150px;
    width: 825px;
    height: 471px;
    border-radius: 26px;
    overflow: hidden;
  }
  .card-front { top: 98px; background: var(--card-white); }
  .card-back {
    top: 631px;
    background: radial-gradient(ellipse 520px 420px at 428px 206px, var(--back-light) 0%, var(--back-mid) 45%, var(--back-dark) 100%);
  }
  .brand-mark {
    position: absolute;
    left: 540px; top: 40px;
    width: 136px; height: 136px;
    border-radius: 50%;
    border: 11px solid var(--brand-blue);
  }
  .brand-name {
    position: absolute;
    font-weight: 500;
    font-size: 47px;
    letter-spacing: 1px;
    line-height: 1;
    white-space: nowrap;
  }
  .card-front .brand-name { left: 436px; top: 192px; color: var(--brand-blue); }
  .holder-name {
    position: absolute; left: 49px; top: 277px;
    font-weight: 700; font-size: 31px; letter-spacing: 1px;
    color: var(--name-blue);
  }
  .holder-title {
    position: absolute; left: 50px; top: 315px;
    font-weight: 700; font-size: 21px; letter-spacing: .5px;
    color: var(--title-grey);
  }
  .contact-list {
    position: absolute; left: 50px; top: 351px;
    list-style: none;
  }
  .contact-list li {
    display: flex; align-items: center;
    height: 27px;
    font-size: 20px; color: var(--text-grey);
  }
  .contact-list svg { width: 20px; height: 20px; margin-right: 12px; fill: var(--name-blue); }
  .symbol-area {
    position: absolute; left: 10px; top: 0;
    width: 420px; height: 471px;
    background: radial-gradient(ellipse at 60% 45%, rgba(255,255,255,.22), rgba(255,255,255,0) 70%);
  }
  .card-back .brand-name { left: 432px; top: 338px; color: var(--card-white); }
  .back-url {
    position: absolute; left: 434px; top: 400px;
    font-size: 18px; letter-spacing: 6.2px;
    color: var(--card-white);
  }
</style>
</head>
<body>
  <section class="card card-front">
    <div class="brand-mark"></div>
    <div class="brand-name">TALKHARBOR</div>
    <div class="holder-name">OWEN HALE</div>
    <div class="holder-title">CEO/FOUNDER</div>
    <ul class="contact-list">
      <li>
        <svg viewBox="0 0 20 20"><path d="M6 1h8a1.5 1.5 0 0 1 1.5 1.5v15A1.5 1.5 0 0 1 14 19H6a1.5 1.5 0 0 1-1.5-1.5v-15A1.5 1.5 0 0 1 6 1zm.5 2.5v11h7v-11zM10 15.5a1 1 0 1 0 0 2 1 1 0 0 0 0-2z"/></svg>
        689 512 7043
      </li>
      <li>
        <svg viewBox="0 0 20 20"><path d="M2 5h16v10H2zm1.5 1.5L10 11l6.5-4.5v-.1h-13z"/></svg>
        Info@talkharbor.co.uk
      </li>
      <li>
        <svg viewBox="0 0 20 20"><path d="M10 1.5a8.5 8.5 0 1 0 0 17 8.5 8.5 0 0 0 0-17zm-2 3 2 1.5-1 2-3 .5-1-2a6.5 6.5 0 0 1 3-2zm5 2 2.3 1A6.5 6.5 0 0 1 12 16l-1-3 2-2-1-2z"/></svg>
        www.talkharbor.co.uk
      </li>
    </ul>
  </section>

  <section class="card card-back">
    <div class="symbol-area" role="img" aria-label="Large brand symbol area"></div>
    <div class="brand-name">TALKHARBOR</div>
    <div class="back-url">www.talkharbor.co.uk</div>
  </section>
</body>
</html>
```